Resposive web site in 4 languages + image gallery + logo design

We need a web page, which will work on all devices.
I have uploaded web page concept.
Company name: Praxelun
Industry/Entity Type
It Company
Logo Text
quality matters
Coding
Coded - Design and coding required
Number of Pages Required
1 page

```html
<!DOCTYPE html>
<html lang="en">
<head>
<meta charset="utf-8">
<title>Praxelun</title>
<link href="https://fonts.googleapis.com/css2?family=Cinzel:wght@400;700&family=Lato:wght@400;700&display=swap" rel="stylesheet">
<style>
:root{
  --orange:#f7860f;
  --ink:#1e1e1e;
  --text:#3a3a3a;
  --white:#ffffff;
  --footer:#2a2522;
  --line:#cfcfcf;
}
*{box-sizing:border-box;margin:0;padding:0}
html,body{width:681px;height:1200px;overflow:hidden}
body{position:relative;background:var(--white);font-family:"Lato",sans-serif;color:var(--text)}
.abs{position:absolute}
.top-bar{left:0;top:0;width:681px;height:19px;background:var(--orange)}
.lang{top:3px;width:13px;height:13px;border-radius:50%;background:#f3f3f3;border:1px solid #fff}
.follow{left:533px;top:3px;font-size:9px;font-weight:700;color:var(--white)}
.follow-dot{left:576px;top:3px;width:13px;height:13px;border-radius:50%;background:#3b64b0}
.brand-square{left:93px;top:37px;width:18px;height:18px;background:var(--orange)}
.brand{left:118px;top:33px;font-family:"Lato",sans-serif;font-weight:700;font-size:22px;line-height:26px;color:var(--ink);letter-spacing:.5px}
.nav{top:35px;height:21px;font-size:9px;color:var(--ink);line-height:21px}
.nav.active{background:var(--orange);color:var(--white);padding:0 9px;border-radius:3px}
.hero{left:0;top:71px;width:681px;height:298px;background:linear-gradient(160deg,#5d5a55 0%,#4a4d3e 35%,#6d7a3a 70%,#3c4d22 100%)}
.arrow{width:18px;height:32px}
.estimate-band{left:0;top:337px;width:681px;height:32px;background:rgba(15,15,15,.72)}
.estimate-text{left:102px;top:343px;font-family:"Cinzel",serif;font-size:16px;color:var(--white);letter-spacing:.5px}
.quote-btn{left:446px;top:341px;width:116px;height:24px;border:1px solid #ffd2a0;background:var(--orange);color:var(--white);font-family:"Cinzel",serif;font-size:15px;text-align:center;line-height:22px}
.tile{top:396px;height:118px}
.tile-label{left:0;bottom:0;width:100%;height:22px;background:rgba(10,10,10,.75);color:var(--white);font-family:"Cinzel",serif;font-size:13px;line-height:22px;padding-left:9px}
.tile-plus{right:0;bottom:0;width:0;height:0;border-left:20px solid transparent;border-bottom:20px solid var(--orange)}
.tile-plus span{position:absolute;right:2px;top:5px;color:#fff;font-size:10px;font-weight:700}
.section-title{left:0;width:681px;text-align:center;font-family:"Cinzel",serif;font-size:18px;color:var(--ink);letter-spacing:1px}
.section-title em{font-style:normal;color:var(--orange)}
.title-rule{left:261px;width:160px;border-top:1px dotted #b8b8b8}
.about-lead{left:0;top:582px;width:681px;text-align:center;font-size:7.4px;font-weight:700;color:var(--ink)}
.about-body{left:95px;top:595px;width:491px;text-align:center;font-size:7.4px;line-height:11.5px}
.read-more{left:313px;top:626px;width:55px;height:17px;background:var(--orange);color:var(--white);font-size:7.5px;font-weight:700;text-align:center;line-height:17px;border-radius:2px}
.shot{overflow:hidden}
.shot-caption{left:0;top:56px;width:100%;text-align:center;color:var(--white)}
.shot-caption h3{font-family:"Cinzel",serif;font-weight:400;font-size:11px}
.shot-caption p{font-size:6.5px;line-height:9.5px;margin-top:6px;padding:0 22px}
.footer{left:0;top:998px;width:681px;height:180px;background:linear-gradient(180deg,#25221f,#3a322b 55%,#2a2521)}
.f-head{top:1030px;font-family:"Cinzel",serif;font-size:10px;color:var(--white);letter-spacing:.5px}
.f-icon{top:1030px;width:10px;height:11px;border:1.5px solid var(--orange);border-radius:2px}
.field{height:21px;border:1px solid #d8d8d8;color:var(--white);font-size:7.5px;padding:5px 6px}
.submit{left:273px;top:1140px;width:52px;height:18px;background:var(--orange);color:var(--white);font-family:"Cinzel",serif;font-weight:700;font-size:10px;text-align:center;line-height:18px;border-radius:2px}
.f-rule{top:1046px;border-top:1px dotted #7a7a7a}
.links{left:366px;top:1051px;list-style:none;font-size:7.2px;color:var(--white);line-height:13px}
.links li::before{content:"›";margin-right:6px;margin-left:-11px;color:#bbb}
.links li.on{color:var(--orange);font-weight:700}
.contact{left:486px;font-size:7.2px;color:var(--white);line-height:11px}
.bottom-bar{left:0;top:1178px;width:681px;height:22px;background:var(--orange);color:var(--white);font-size:6.5px;font-weight:700;text-align:center;line-height:22px}
</style>
</head>
<body>
<div class="abs top-bar"></div>
<div class="abs lang" style="left:452px"></div>
<div class="abs lang" style="left:470px"></div>
<div class="abs lang" style="left:488px"></div>
<div class="abs lang" style="left:506px"></div>
<div class="abs follow">Follow Us</div>
<div class="abs follow-dot"></div>

<div class="abs brand-square"></div>
<div class="abs brand">Praxelun</div>
<div class="abs nav active" style="left:368px">HOME</div>
<div class="abs nav" style="left:423px">ABOUT US</div>
<div class="abs nav" style="left:484px">SERVICES</div>
<div class="abs nav" style="left:533px">CONTACT US</div>

<div class="abs hero" role="img" aria-label="Stone house with a smiling family and dog on the lawn"></div>
<svg class="abs arrow" style="left:44px;top:188px" viewBox="0 0 18 32"><path d="M15 2 2 16l13 14" fill="none" stroke="#fff" stroke-width="1.5"/></svg>
<svg class="abs arrow" style="left:624px;top:188px" viewBox="0 0 18 32"><path d="M3 2l13 14L3 30" fill="none" stroke="#fff" stroke-width="1.5"/></svg>
<div class="abs estimate-band"></div>
<div class="abs estimate-text">ARE YOU INTERESTED IN AN ESTIMATE?</div>
<div class="abs quote-btn">Get A Quote</div>

<div class="abs tile" style="left:91px;width:162px;background:linear-gradient(160deg,#8fb0c8,#c98a3e 45%,#7a5020)" role="img" aria-label="Wooden log house">
  <div class="abs tile-label">WOODWORKS</div><div class="abs tile-plus"><span>+</span></div>
</div>
<div class="abs tile" style="left:259px;width:162px;background:linear-gradient(160deg,#d9e4ec,#8a7a66 45%,#4d4436)" role="img" aria-label="Natural stone cottage">
  <div class="abs tile-label">STONE WORKS</div><div class="abs tile-plus"><span>+</span></div>
</div>
<div class="abs tile" style="left:428px;width:161px;background:linear-gradient(160deg,#e6e8ea,#8c8175 50%,#5a6a48)" role="img" aria-label="Stone house under restoration with scaffolding">
  <div class="abs tile-label">RESTORATION</div><div class="abs tile-plus"><span>+</span></div>
</div>

<div class="abs section-title" style="top:548px">ABOUT <em>PRAXELUN</em></div>
<div class="abs title-rule" style="top:573px"></div>
<div class="abs about-lead">Praxelun Is A Company Whose Business Operations Include Making Wooden Products, Restoration And Building Structures From Natural Stone.</div>
<div class="abs about-body">All of our products are made by craftsmen and specialists who have extensive experience and knowledge in their fields. The products we offer are always handmade and we take the requests and ideas of the specific client into account We always strive to achieve the best possible quality.</div>
<div class="abs read-more">READ MORE</div>

<div class="abs section-title" style="top:680px">PROJECT <em>GALLERY</em></div>
<div class="abs title-rule" style="top:705px"></div>

<svg class="abs arrow" style="left:60px;top:845px" viewBox="0 0 18 32"><path d="M15 2 2 16l13 14" fill="none" stroke="#333" stroke-width="1.2"/></svg>
<svg class="abs arrow" style="left:603px;top:845px" viewBox="0 0 18 32"><path d="M3 2l13 14L3 30" fill="none" stroke="#333" stroke-width="1.2"/></svg>

<div class="abs shot" style="left:91px;top:716px;width:180px;height:153px;background:linear-gradient(160deg,#3a2618,#6b4527 50%,#2a1c12)" role="img" aria-label="Timber frame porch at dusk">
  <div class="abs shot-caption"><h3>LOREM IPSUM</h3><p>Lorem ipsum dolor sit amet, consectetuer adipiscing elit, sed diam nonummy nibh eu</p></div>
</div>
<div class="abs shot" style="left:275px;top:716px;width:188px;height:72px;background:linear-gradient(180deg,#d8dee2,#7d8a70 55%,#4e7a2c)" role="img" aria-label="House with curved stone retaining wall"></div>
<div class="abs shot" style="left:275px;top:792px;width:92px;height:77px;background:linear-gradient(160deg,#dfe4e8,#9a5a3a 50%,#5d3a26)" role="img" aria-label="Brick and stone house front"></div>
<div class="abs shot" style="left:372px;top:792px;width:91px;height:77px;background:linear-gradient(170deg,#e8eaec,#8e8e8a 55%,#6a6a64)" role="img" aria-label="Grey stone house with garage"></div>
<div class="abs shot" style="left:467px;top:716px;width:122px;height:153px;background:linear-gradient(160deg,#c7cacc,#6d6a66 50%,#4d6a34)" role="img" aria-label="Stone house corner with garden"></div>
<div class="abs shot" style="left:91px;top:873px;width:276px;height:104px;background:linear-gradient(170deg,#c9ccd0,#a08054 45%,#8a2a24 70%,#5a4a36)" role="img" aria-label="Log house with red roof in winter"></div>
<div class="abs shot" style="left:371px;top:873px;width:218px;height:104px;background:linear-gradient(120deg,#7a2c0c,#c4641e 50%,#8a3a12)" role="img" aria-label="Wooden staircase and interior woodwork"></div>

<div class="abs footer" role="img" aria-label="Dimmed evening photo of a stone house"></div>
<div class="abs f-icon" style="left:99px"></div>
<div class="abs f-head" style="left:118px">QUICK INQUIRY</div>
<div class="abs field" style="left:98px;top:1053px;width:227px">Name</div>
<div class="abs field" style="left:98px;top:1083px;width:107px">Phone</div>
<div class="abs field" style="left:218px;top:1083px;width:107px">Email</div>
<div class="abs field" style="left:98px;top:1112px;width:227px">Message</div>
<div class="abs submit">SUBMIT</div>

<div class="abs f-icon" style="left:352px"></div>
<div class="abs f-head" style="left:366px">QUICK LINKS</div>
<div class="abs f-rule" style="left:352px;width:92px"></div>
<ul class="abs links">
  <li class="on">Home</li><li>About Us</li><li>Services</li><li>Contact Us</li>
</ul>

<div class="abs f-icon" style="left:473px;border-radius:50%"></div>
<div class="abs f-head" style="left:491px">CONTACT DETAILS</div>
<div class="abs f-rule" style="left:473px;width:110px"></div>
<svg class="abs" style="left:474px;top:1053px" width="8" height="11" viewBox="0 0 8 11"><path d="M4 0a4 4 0 0 1 4 4c0 3-4 7-4 7S0 7 0 4a4 4 0 0 1 4-4z" fill="#f7860f"/><circle cx="4" cy="4" r="1.5" fill="#2a2521"/></svg>
<div class="abs contact" style="top:1054px">Velmara 12<br>10415 Korvik<br>ESTONIA</div>
<svg class="abs" style="left:474px;top:1091px" width="9" height="9" viewBox="0 0 9 9"><path d="M1 1l2-0.5 1.2 2.2-1 1a5 5 0 0 0 2 2l1-1 2.2 1.2L8 8C4 8 1 5 1 1z" fill="#f7860f"/></svg>
<div class="abs contact" style="top:1091px;font-weight:700">+372 55 01842</div>
<svg class="abs" style="left:474px;top:1110px" width="9" height="7" viewBox="0 0 9 7"><rect width="9" height="7" fill="#f7860f"/><path d="M0 0l4.5 4L9 0" fill="none" stroke="#2a2521" stroke-width=".8"/></svg>
<div class="abs contact" style="top:1108px">sales@praxelun.com</div>

<div class="abs bottom-bar">Copyright © 2016 Praxelun. All Right Reserved.</div>
</body>
</html>
```